Pellowar

We need logo and wesbsite for a software development company based out of Hyderabad, India focused on startups and mid sized companies focused on build a new software products in USA and Europe countires.

Target Market(s)

startup and midsized companies in teh USA and Europe for software product development.

Industry/Entity Type

software development

Coding

Coded - Design and coding required

Number of Pages Required

5+ page

Requirements
Must have
• latest design concepts and very elegant
Nice to have
• each page should have images that reflects the content
Should not have
• too many colors

```html
<!DOCTYPE html>
<html lang="en">
<head>
<meta charset="utf-8">
<title>Pellowar — Software Product Development</title>
<link href="https://fonts.googleapis.com/css2?family=Open+Sans:wght@400;600;700&family=Lato:wght@400;700&display=swap" rel="stylesheet">
<style>
:root{
  --orange:#f05a22;
  --orange-soft:#f7a27f;
  --ink:#111111;
  --text:#2b2b2b;
  --muted:#555555;
  --band:#eef0f3;
  --white:#ffffff;
  --footer:#000000;
}
*{margin:0;padding:0;box-sizing:border-box}
html,body{width:1200px;height:4158px;overflow:hidden}
body{position:relative;background:var(--white);font-family:'Lato',sans-serif;color:var(--text)}
.abs{position:absolute}
.heading{font-family:'Open Sans',sans-serif;color:var(--ink);font-weight:400}
.btn{position:absolute;display:flex;align-items:center;justify-content:center;background:var(--orange);color:var(--white);border-radius:30px;font-family:'Open Sans',sans-serif;font-weight:600;font-size:15px;text-decoration:none}
.btn-white{background:var(--white);color:var(--orange)}

/* nav */
.site-nav{position:absolute;top:0;left:0;width:1200px;height:84px;background:var(--white)}
.logo{position:absolute;font-family:'Open Sans',sans-serif;font-weight:700;color:var(--ink);letter-spacing:-0.5px}
.site-nav .logo{left:110px;top:20px;font-size:28px}
.nav-links a{position:absolute;top:29px;font-family:'Open Sans',sans-serif;font-size:15px;color:var(--text);text-decoration:none}

/* hero */
.hero{position:absolute;top:84px;left:0;width:1200px;height:626px;background:linear-gradient(120deg,#1b1d22 0%,#2b3036 45%,#3a3f45 70%,#23262b 100%)}
.hero-shade{position:absolute;inset:0;background:linear-gradient(90deg,rgba(0,0,0,.45),rgba(0,0,0,.1))}
.hero h1{position:absolute;left:110px;top:168px;font-family:'Open Sans',sans-serif;font-weight:400;font-size:52px;color:var(--white)}
.hero p{position:absolute;left:110px;top:237px;width:520px;font-size:15px;line-height:26px;color:var(--white)}
.wave{position:absolute;left:0}

/* product */
.section-title{position:absolute;left:0;width:1200px;text-align:center;font-size:35px}
.section-lead{position:absolute;left:240px;width:720px;text-align:center;font-size:15px;line-height:26px;color:var(--text)}
.role-card{position:absolute;top:922px;width:236px;height:325px;border-radius:6px;overflow:hidden}
.role-card .photo{position:absolute;inset:0}
.role-card h3{position:absolute;left:0;top:185px;width:100%;text-align:center;font-family:'Open Sans',sans-serif;font-weight:400;font-size:22px;color:var(--white)}
.role-card p{position:absolute;left:18px;top:224px;width:200px;text-align:center;font-size:14.5px;line-height:26px;color:var(--white)}

/* about */
.about{position:absolute;top:1440px;left:0;width:1200px;height:660px;background:var(--band)}
.eyebrow{position:absolute;font-family:'Open Sans',sans-serif;font-size:18px;color:var(--orange)}
.about h2{position:absolute;left:112px;top:136px;font-size:34px;line-height:41px}
.about p{position:absolute;left:112px;top:242px;width:465px;font-size:14.5px;line-height:25.8px;color:var(--ink)}
.hex{position:absolute;clip-path:polygon(50% 0,100% 25%,100% 75%,50% 100%,0 75%,0 25%)}

/* team */
.team-card{position:absolute;top:2277px;width:306px;height:355px}
.team-card svg.shape{position:absolute;inset:0;filter:drop-shadow(0 4px 14px rgba(0,0,0,.08))}
.team-card .icon{position:absolute;left:103px;top:54px}
.team-card h3{position:absolute;left:0;top:152px;width:100%;text-align:center;font-family:'Open Sans',sans-serif;font-weight:600;font-size:19px;color:var(--ink)}
.team-card p{position:absolute;left:24px;top:194px;width:258px;text-align:center;font-size:14px;line-height:26px;color:var(--text)}
.more-link{position:absolute;left:0;top:280px;width:100%;text-align:center;font-family:'Open Sans',sans-serif;font-size:15px;color:var(--orange)}

/* case study */
.case{position:absolute;top:2710px;left:0;width:1200px;height:412px;background:linear-gradient(100deg,#e2531f 0%,#f0642e 45%,#e85a24 70%,#d9501d 100%)}
.case h2{position:absolute;left:0;top:80px;width:1200px;text-align:center;color:var(--white);font-size:35px}
.case p{position:absolute;left:100px;top:140px;width:1000px;text-align:center;font-size:14.5px;line-height:26px;color:var(--white)}

/* testimonials */
.quote-mark{position:absolute;width:70px;height:70px;border-radius:50%;background:var(--orange);color:var(--white);display:flex;align-items:center;justify-content:center;font-family:'Open Sans',sans-serif;font-weight:700;font-size:30px}
.testimonial-text{position:absolute;top:3339px;width:310px;font-size:14.5px;line-height:26.5px;color:var(--text)}
.avatar{position:absolute;width:64px;height:64px;border-radius:50%;background:linear-gradient(135deg,#8a8f96,#3e4249)}
.client-name{position:absolute;top:3550px;font-family:'Open Sans',sans-serif;font-size:20px;color:var(--orange)}
.client-role{position:absolute;top:3580px;font-size:14.5px;color:var(--muted)}

/* footer */
.footer{position:absolute;top:3700px;left:0;width:1200px;height:458px;background:var(--footer);color:var(--white)}
.footer .logo{left:110px;top:140px;font-size:38px;color:var(--white)}
.footer-about{position:absolute;left:110px;top:206px;width:300px;font-size:14.5px;line-height:26px}
.footer h4{position:absolute;top:128px;font-family:'Open Sans',sans-serif;font-weight:400;font-size:21px}
.footer ul{position:absolute;top:174px;list-style:none;font-size:14.5px}
.footer li{height:30px;display:flex;align-items:flex-start;gap:10px}
.footer li::before{content:"«";color:var(--white)}
.footer .contact li::before{content:none}
.footer .contact li{height:auto;margin-bottom:14px;line-height:24px}
.divider{position:absolute;left:110px;top:360px;width:980px;height:1px;background:#222}
.copyright{position:absolute;left:0;top:397px;width:1200px;text-align:center;font-size:15px}
</style>
</head>
<body>

<header class="site-nav">
  <div class="logo">Pellowar</div>
  <nav class="nav-links">
    <a style="left:334px">Home</a>
    <a style="left:439px">About</a>
    <a style="left:502px">Build Ur Product</a>
    <a style="left:661px">Build Your Team</a>
    <a style="left:819px">Case Study</a>
  </nav>
  <a class="btn" style="left:938px;top:16px;width:151px;height:44px">Contact Us</a>
</header>

<section class="hero" role="img" aria-label="Developer working at laptops with code on screens">
  <div class="hero-shade"></div>
  <h1>Welcome To Pellowar</h1>
  <p>Teams are the essence of every business. They can create wonders if built with perfection. We are a group of entrepreneurs,</p>
  <a class="btn" style="left:111px;top:312px;width:151px;height:50px">Get Started</a>
</section>
<svg class="wave" style="top:610px" width="1200" height="110" viewBox="0 0 1200 110">
  <path d="M0 85 C90 30 200 20 330 60 C470 100 560 110 700 70 C850 25 1000 5 1200 50 L1200 110 L0 110Z" fill="var(--orange)"/>
  <path d="M0 98 C90 45 200 35 330 75 C470 115 560 120 700 85 C850 42 1000 22 1200 66 L1200 110 L0 110Z" fill="var(--white)"/>
</svg>

<h2 class="section-title heading" style="top:785px">Build Your Product</h2>
<p class="section-lead" style="top:843px">As startups are racing to build software as a product, they have stumbling blocks on building software from scratch. One of the reasons is stiff competition.</p>

<article class="role-card" style="left:111px">
  <div class="photo" role="img" aria-label="Project manager with colleagues" style="background:linear-gradient(180deg,#5a5e64 0%,#2c2e32 55%,#050505 100%)"></div>
  <h3>Project Manager</h3><p>Lorem ipsum dolor sit amet, consectetur adipiscing elit, sed do eiusmod.</p>
</article>
<article class="role-card" style="left:359px">
  <div class="photo" role="img" aria-label="Team lead presenting to a team" style="background:linear-gradient(180deg,#8c7b6e 0%,#b76a45 50%,#f05a22 100%)"></div>
  <h3>Team Lead</h3><p>Lorem ipsum dolor sit amet, consectetur adipiscing elit, sed do eiusmod.</p>
</article>
<article class="role-card" style="left:606px">
  <div class="photo" role="img" aria-label="Business analyst beside an analytics screen" style="background:linear-gradient(180deg,#a09c8e 0%,#5b5a52 50%,#070707 100%)"></div>
  <h3>Business analyst</h3><p>Lorem ipsum dolor sit amet, consectetur adipiscing elit, sed do eiusmod.</p>
</article>
<article class="role-card" style="left:853px">
  <div class="photo" role="img" aria-label="Developers coding at monitors" style="background:linear-gradient(180deg,#4a5560 0%,#262c33 50%,#040404 100%)"></div>
  <h3>Developers</h3><p>Lorem ipsum dolor sit amet, consectetur adipiscing elit, sed do eiusmod.</p>
</article>

<a class="btn" style="left:539px;top:1313px;width:121px;height:52px">View All</a>

<section class="about">
  <div class="eyebrow" style="left:115px;top:105px">About Pellowar</div>
  <h2 class="heading">Teams are the essence<br>of every business.</h2>
  <p>They can create wonders if built with perfection.<br>We are a group of entrepreneurs, technocrats, software architects, and delivery heads who have come together to serve startups, product companies, and enterprises with their product development. We are prompt in understanding your product and help design, build, maintain and operate your product. Pellowar quickly set up a team of UX experts, Business Analysts, Developers and QA resources to build the best team to deliver the product.</p>
  <a class="btn" style="left:110px;top:498px;width:144px;height:52px">Learn More</a>
  <div class="hex" role="img" aria-label="Developer at a desktop computer in an office" style="left:688px;top:78px;width:404px;height:469px;background:linear-gradient(135deg,#e9e6e1 0%,#b9b6b0 40%,#6d6a66 100%)"></div>
  <div class="hex" style="left:588px;top:366px;width:193px;height:224px;background:var(--white)"></div>
  <div class="hex" role="img" aria-label="Team meeting video preview" style="left:594px;top:373px;width:181px;height:210px;background:linear-gradient(135deg,#d9652f,#f07a44 60%,#c84f1d)"></div>
  <svg class="abs" style="left:655px;top:449px" width="58" height="58" viewBox="0 0 58 58">
    <circle cx="29" cy="29" r="29" fill="var(--white)"/>
    <path d="M24 20 L38 29 L24 38Z" fill="var(--orange)"/>
  </svg>
</section>

<div class="eyebrow" style="left:0;width:1200px;text-align:center;top:2177px">Our Team</div>
<h2 class="section-title heading" style="top:2202px">Build Your Team</h2>

<article class="team-card" style="left:111px">
  <svg class="shape" width="306" height="355" viewBox="0 0 306 355"><polygon points="153,0 306,70 306,285 153,355 0,285 0,70" fill="var(--white)"/></svg>
  <svg class="icon" width="100" height="76" viewBox="0 0 100 76"><circle cx="30" cy="38" r="36" fill="var(--orange-soft)"/><circle cx="38" cy="38" r="38" fill="var(--orange)"/><rect x="24" y="26" width="28" height="22" rx="2" fill="none" stroke="var(--white)" stroke-width="2"/><path d="M29 33h18M29 38h18M29 43h10" stroke="var(--white)" stroke-width="2"/></svg>
  <h3>Pass cognitive aptitude test.</h3>
  <p>Accepting job applications from the entire world means every role on Pellowar receives thousands of</p>
  <div class="more-link">Leran More ➔</div>
</article>
<article class="team-card" style="left:449px">
  <svg class="shape" width="306" height="355" viewBox="0 0 306 355"><polygon points="153,0 306,70 306,285 153,355 0,285 0,70" fill="var(--white)"/></svg>
  <svg class="icon" width="100" height="76" viewBox="0 0 100 76"><circle cx="30" cy="38" r="36" fill="var(--orange-soft)"/><circle cx="38" cy="38" r="38" fill="var(--orange)"/><circle cx="38" cy="38" r="11" fill="none" stroke="var(--white)" stroke-width="2"/><path d="M38 20v7M38 49v7M20 38h7M49 38h7M26 26l5 5M45 45l5 5M50 26l-5 5M31 45l-5 5" stroke="var(--white)" stroke-width="2"/></svg>
  <h3>Pass English proficiency test</h3>
  <p>Someday, technological advancements will make it possible for teams to collaborate without</p>
  <div class="more-link">Leran More ➔</div>
</article>
<article class="team-card" style="left:785px">
  <svg class="shape" width="306" height="355" viewBox="0 0 306 355"><polygon points="153,0 306,70 306,285 153,355 0,285 0,70" fill="var(--white)"/></svg>
  <svg class="icon" width="100" height="76" viewBox="0 0 100 76"><circle cx="30" cy="38" r="36" fill="var(--orange-soft)"/><circle cx="38" cy="38" r="38" fill="var(--orange)"/><rect x="23" y="25" width="30" height="20" rx="2" fill="none" stroke="var(--white)" stroke-width="2"/><path d="M19 49h38" stroke="var(--white)" stroke-width="2.5"/><path d="M30 32l-3 3 3 3M46 32l3 3-3 3" fill="none" stroke="var(--white)" stroke-width="2"/></svg>
  <h3>Prove real-world job skills.</h3>
  <p>Of course, there's much more to being a great worker than intelligence and language skills.</p>
  <div class="more-link">Leran More ➔</div>
</article>

<section class="case" role="img" aria-label="Orange toned background of binary code">
  <h2 class="heading">Case study</h2>
  <p>Many business owners have great ideas but no experience with the actual product. Once you have an idea in mind, you will require software development aid at some point – whether your concept is for next-generation software or an inventive approach to offering an existing service. It might also be the development of a mobile app or web-based software. Whatever product you're working on, you'll need a technical co-founder to help you get it off the ground. An MVP can help you turn your vision into reality.</p>
  <a class="btn btn-white" style="left:539px;top:270px;width:143px;height:51px">Learn More</a>
</section>

<h2 class="section-title heading" style="top:3180px;left:30px">Client Testimonials</h2>

<svg class="abs" style="left:110px;top:3434px" width="46" height="16" viewBox="0 0 46 16"><path d="M46 8H3M10 2L2 8l8 6" fill="none" stroke="var(--orange-soft)" stroke-width="2"/></svg>
<svg class="abs" style="left:1040px;top:3434px" width="46" height="16" viewBox="0 0 46 16"><path d="M0 8h43M36 2l8 6-8 6" fill="none" stroke="var(--orange)" stroke-width="2"/></svg>

<div class="quote-mark" style="left:214px;top:3294px">“</div>
<p class="testimonial-text" style="left:265px">Lorem ipsum dolor sit amet, consectetur adipiscing elit, sed do eiusmod tempor inci-didunt ut labore et dolore magna aliqua. Ut enim ad minim veniam, quis nostrud exerci-tation ullamco laboris nisi ut aliquip ex ea commodo consequat. Duis aute irure dolor in reprehenderit</p>
<div class="avatar" role="img" aria-label="Client portrait" style="left:259px;top:3542px"></div>
<div class="client-name" style="left:336px">Marlow Keaton</div>
<div class="client-role" style="left:336px">Lorem ipsum dolor</div>

<div class="quote-mark" style="left:614px;top:3294px">“</div>
<p class="testimonial-text" style="left:664px">Lorem ipsum dolor sit amet, consectetur adipiscing elit, sed do eiusmod tempor inci-didunt ut labore et dolore magna aliqua. Ut enim ad minim veniam, quis nostrud exerci-tation ullamco laboris nisi ut aliquip ex ea commodo consequat. Duis aute irure dolor in reprehenderit</p>
<div class="avatar" role="img" aria-label="Client portrait" style="left:659px;top:3542px"></div>
<div class="client-name" style="left:736px">Marlow Keaton</div>
<div class="client-role" style="left:736px">Lorem ipsum dolor</div>

<svg class="wave" style="top:3640px" width="1200" height="70" viewBox="0 0 1200 70">
  <path d="M0 30 C150 60 300 75 450 45 C560 20 640 0 760 20 C900 45 1050 65 1200 40 L1200 70 L0 70Z" fill="var(--orange)"/>
  <path d="M0 42 C150 72 300 85 450 56 C560 32 640 14 760 32 C900 56 1050 76 1200 52 L1200 70 L0 70Z" fill="var(--footer)"/>
</svg>

<footer class="footer">
  <div class="logo">Pellowar</div>
  <p class="footer-about">Lorem ipsum dolor sit amet, consectetur adipiscing elit, sed do eiusmod tempor incididunt ut labore et dolore magna aliqua. Ut enim ad minim veniam</p>

  <h4 style="left:465px">Quick Link</h4>
  <ul style="left:465px"><li>Home</li><li>About</li><li>Build Ur Product</li><li>Build Your Team</li><li>Case Study</li></ul>

  <h4 style="left:672px">Services</h4>
  <ul style="left:672px"><li>Terms&amp;condtions</li><li>Privacy Policy</li><li>About Us</li><li>Support</li></ul>

  <h4 style="left:887px">Contact Us</h4>
  <ul class="contact" style="left:887px;width:200px">
    <li><svg width="14" height="18" viewBox="0 0 14 18"><path d="M7 1a6 6 0 0 0-6 6c0 4.5 6 10 6 10s6-5.5 6-10a6 6 0 0 0-6-6z" fill="var(--white)"/><circle cx="7" cy="7" r="2.2" fill="var(--footer)"/></svg><span>Lorem ipsum dolor sit amet, consectetur</span></li>
    <li><svg width="14" height="18" viewBox="0 0 14 18"><rect x="0" y="4" width="14" height="10" fill="var(--white)"/><path d="M0 4l7 5 7-5" fill="none" stroke="var(--footer)" stroke-width="1.4"/></svg><span>info@pellowar.com</span></li>
    <li><svg width="14" height="18" viewBox="0 0 14 18"><path d="M3 3l3 0 1 4-2 1c1 2 2 3 4 4l1-2 4 1v3c-6 0-11-5-11-11z" fill="var(--white)"/></svg><span>+1 555 010 4477</span></li>
  </ul>

  <div class="divider"></div>
  <div class="copyright">©Copyrights 2022 Pellowar &nbsp;|&nbsp;&nbsp; All Rights Reserved</div>
</footer>

</body>
</html>
```